Disability Magazine – Cover + Full Inside Layout

About the Publication

Our magazine is a quarterly, high‑impact publication that celebrates the lives, achievements, and everyday experiences of people with disabilities. It aims to inform, inspire, and advocate for accessibility, inclusion, and empowerment across all communities.

Target Audience

Adults (18‑65) with visible or invisible disabilities
Caregivers, family members, and allies
Professionals in health, education, policy, and design fields
Advocates and NGOs focused on accessibility

Project Goals

Visually compelling cover that instantly signals the magazine’s inclusive mission.
Consistent, readable interior layout for feature articles, interviews, photo essays, and resource guides.
Design that works both in print (A4, 300 dpi) and digitally (PDF/online flipbook).

```html
<!DOCTYPE html>
<html lang="en">
<head>
<meta charset="utf-8">
<title>Breaking the Barriers – Magazine Cover and Inside Layout</title>
<link href="https://fonts.googleapis.com/css2?family=Anton&family=Poppins:wght@400;600;700&display=swap" rel="stylesheet">
<style>
:root{
  --bg:#e6e4e6;
  --paper:#f5f5f3;
  --ink:#2a2c2e;
  --ink-soft:#3a3d40;
  --accent:#e3bb8a;
  --rule:#9a9a9a;
  --text:#4a4a4a;
  --white:#ffffff;
}
*{box-sizing:border-box;margin:0;padding:0}
html,body{width:692px;height:1200px;overflow:hidden;background:var(--bg)}
body{font-family:"Poppins",sans-serif;color:var(--text)}
.sheet{width:692px;height:1200px;padding:8px 12px;display:grid;grid-template-columns:326px 326px;grid-template-rows:repeat(5,230px);column-gap:16px;row-gap:8px}
.spread{display:flex;width:326px;height:230px;box-shadow:0 2px 6px rgba(0,0,0,.18)}
.page{position:relative;width:163px;height:230px;background:var(--paper);overflow:hidden}
.page--dark{background:var(--ink);color:#d8d8d8}
.page--left{box-shadow:inset -6px 0 8px -6px rgba(0,0,0,.25)}
.page--right{box-shadow:inset 6px 0 8px -6px rgba(0,0,0,.25)}
.runner{position:absolute;top:8px;left:10px;right:10px;font-family:"Anton",sans-serif;font-size:4px;letter-spacing:.2px;color:var(--ink);border-bottom:.4px solid var(--rule);padding-bottom:2px}
.page--dark .runner{color:var(--white)}
.folio{position:absolute;top:14px;right:10px;width:4px;height:4px;background:var(--ink)}
.page--dark .folio{background:var(--accent)}
.photo{position:absolute}
.box{position:absolute;background:var(--ink);color:#d8d8d8}
.title{font-family:"Anton",sans-serif;font-style:italic;text-transform:uppercase;line-height:1;color:var(--ink);font-size:8px}
.title .hl{color:var(--accent);display:block}
.page--dark .title,.box .title{color:var(--white)}
.copy{position:absolute;font-size:2.7px;line-height:1.4;overflow:hidden}
.copy p{margin-bottom:2px}
.copy b{font-weight:700;display:block;font-size:3px}
.page--dark .copy,.box .copy{color:#cfcfcf}
/* cover */
.cover-back-title{position:absolute;top:12px;left:8px;font-family:"Anton",sans-serif;font-size:17px;line-height:.95;color:var(--ink);text-transform:uppercase}
.cover-front{background:linear-gradient(180deg,#2a2c2e 0%,#3b3d40 50%,#d9d9d9 100%)}
.cover-mast{position:absolute;top:12px;left:8px;font-family:"Anton",sans-serif;font-size:30px;color:var(--white);letter-spacing:.5px}
.cover-tag{position:absolute;top:6px;left:40px;font-size:2.8px;color:var(--white);letter-spacing:.3px}
.cover-lines{position:absolute;top:54px;left:8px;font-family:"Anton",sans-serif;color:var(--white);font-size:6px;line-height:1.05;text-transform:uppercase}
.cover-lines .year{font-size:11px}
.cover-name{position:absolute;right:8px;top:130px;font-family:"Anton",sans-serif;font-size:11px;line-height:.95;color:var(--white);text-align:right}
.cover-excl{position:absolute;left:8px;bottom:14px;font-family:"Anton",sans-serif;color:var(--ink);font-size:9px;line-height:1}
.cover-excl small{display:block;font-family:"Poppins",sans-serif;font-size:3px;letter-spacing:1.5px;font-weight:600}
.brand{position:absolute;right:8px;bottom:10px;font-family:"Anton",sans-serif;font-size:7px;color:var(--ink);letter-spacing:.3px}
/* contents */
.toc{position:absolute;left:78px;top:24px;width:78px}
.toc-item{display:flex;gap:3px;align-items:baseline;margin-top:5px}
.toc-num{font-family:"Anton",sans-serif;font-size:8px;color:var(--ink)}
.toc-item span{font-size:3px;font-weight:600;color:var(--ink)}
.toc-item em{display:block;font-style:normal;font-size:2.4px;font-weight:400;color:var(--text)}
.quote{font-weight:700;font-size:6.5px;line-height:1.15;color:var(--white)}
.vertical{position:absolute;transform:rotate(-90deg);transform-origin:left top;white-space:nowrap}
.bullet::before{content:"▸ ";font-size:2.6px}
</style>
</head>
<body>
<main class="sheet">

<section class="spread">
  <div class="page page--left">
    <h2 class="cover-back-title">Breaking the<br>Barriers</h2>
    <div class="photo" style="left:0;top:52px;width:163px;height:120px;background:linear-gradient(160deg,#6f8a4a,#b9a886 60%,#58683c)" role="img" aria-label="Smiling hiker with a prosthetic leg walking with trekking poles"></div>
    <div class="box" style="right:8px;top:84px;width:44px;height:60px;padding:4px">
      <div class="copy" style="position:static"><b>Lorem ipsum dolor!</b><p>Lorem Ipsum is simply dummy text of the printing industry.</p></div>
    </div>
  </div>
  <div class="page page--right cover-front">
    <p class="cover-tag">LOREM IPSUM IS SIMPLY DUMMY TEXT</p>
    <h1 class="cover-mast">MAGAZINE</h1>
    <p class="cover-lines">The best<br>leadership<br>sports<br><span class="year">2029</span></p>
    <div class="photo" style="left:44px;top:60px;width:86px;height:140px;background:radial-gradient(ellipse at 50% 40%,#bfbfbf,#5a5c5e 70%,rgba(0,0,0,0))" role="img" aria-label="Athlete in a wheelchair raising a trophy"></div>
    <p class="cover-name">NAME<br>HERE</p>
    <p class="cover-excl"><small>EXCLUSIVE</small>NAME HERE</p>
    <p class="brand">ZAVRENTA</p>
  </div>
</section>

<section class="spread">
  <div class="page page--left">
    <div class="photo" style="left:0;top:0;width:72px;height:180px;background:linear-gradient(180deg,#b9dde3,#7d8a8c 50%,#b38a80)" role="img" aria-label="Sprinter with a running blade on a track"></div>
    <p class="runner" style="left:80px">MAGAZINE</p>
    <div class="toc">
      <h2 class="title">Table of<br>Contents</h2>
      <div class="toc-item"><span class="toc-num">04</span><span>LOREM IPSUM<em>Lorem ipsum dolor sit amet</em></span></div>
      <div class="toc-item"><span class="toc-num">05</span><span>LOREM IPSUM<em>Lorem ipsum dolor sit amet</em></span></div>
      <div class="toc-item"><span class="toc-num">06</span><span>LOREM IPSUM<em>Lorem ipsum dolor sit amet</em></span></div>
      <div class="toc-item"><span class="toc-num">07</span><span>LOREM IPSUM<em>Lorem ipsum dolor sit amet</em></span></div>
      <div class="toc-item"><span class="toc-num">08</span><span>LOREM IPSUM<em>Lorem ipsum dolor sit amet</em></span></div>
      <div class="toc-item"><span class="toc-num">09</span><span>LOREM IPSUM<em>Lorem ipsum dolor sit amet</em></span></div>
    </div>
    <div class="box" style="left:40px;right:0;bottom:0;height:40px;padding:6px 8px">
      <p style="font-family:'Anton',sans-serif;font-size:4px;color:var(--accent);line-height:1.3">LOREM IPSUM DOLOR SIT AMET, CONSECTETUR ADIPISCING ELIT, SED DO EIUSMOD TEMPOR INCIDIDUNT UT LABORE ET DOLORE MAGNA ALIQUA.</p>
    </div>
  </div>
  <div class="page page--right">
    <p class="runner">MAGAZINE</p><span class="folio"></span>
    <div class="photo" style="left:10px;top:24px;width:143px;height:170px;background:linear-gradient(160deg,#d6e2e4,#74904e 45%,#a89878)" role="img" aria-label="Hiker with a prosthetic leg smiling on a trail"></div>
    <div class="box" style="right:10px;bottom:18px;width:56px;height:80px;padding:6px">
      <div class="copy" style="position:static"><b style="color:var(--accent)">Lorem Ipsum is simply</b><p>Lorem Ipsum is simply dummy text of the printing and typesetting industry. Lorem Ipsum has been the industry's standard dummy text ever since the 1500s, when an unknown.</p></div>
    </div>
  </div>
</section>

<section class="spread">
  <div class="page page--left">
    <p class="runner">MAGAZINE</p>
    <h2 class="title" style="position:absolute;left:12px;top:20px">Articles<br>Content Here</h2>
    <div class="copy" style="left:12px;top:42px;width:62px;height:150px">
      <p>Lorem Ipsum is simply dummy text of the printing and typesetting industry. Lorem Ipsum has been the industry's standard.</p>
      <b>Lorem Ipsum is simply dummy</b>
      <p>Lorem Ipsum is simply dummy text of the printing and typesetting industry. Lorem Ipsum has been the industry's standard dummy text ever since the 1500s, when an unknown.</p>
      <p>Lorem Ipsum is simply dummy text of the printing and typesetting industry. Lorem Ipsum has been the industry's standard dummy text ever since the 1500s.</p>
    </div>
    <div class="photo" style="left:80px;top:40px;width:83px;height:70px;background:linear-gradient(150deg,#9ab0b6,#8a8e62 60%,#4f5a38)" role="img" aria-label="Archer in a wheelchair drawing a bow outdoors"></div>
    <div class="copy" style="left:80px;top:116px;width:72px;height:90px">
      <b>Lorem Ipsum is simply dummy</b>
      <p>Lorem Ipsum is simply dummy text of the printing and typesetting industry. Lorem Ipsum has been the industry's standard dummy text ever since the 1500s.</p>
    </div>
  </div>
  <div class="page page--right">
    <p class="runner">MAGAZINE</p><span class="folio"></span>
    <div class="photo" style="left:0;top:20px;width:110px;height:70px;background:linear-gradient(150deg,#a7a77c,#6e7142 60%,#c8b68e)" role="img" aria-label="Sunlit trees in a park behind the archer"></div>
    <div class="box" style="right:10px;top:28px;width:52px;height:150px;padding:6px">
      <div class="copy" style="position:static"><b style="color:var(--accent)">Lorem Ipsum is simply</b><p>Lorem Ipsum is simply dummy text of the printing and typesetting industry.</p><b style="color:var(--accent)">Lorem Ipsum is simply</b><p>Lorem Ipsum has been the industry's standard dummy text ever since the 1500s.</p><b style="color:var(--accent)">Lorem Ipsum is simply</b><p>Lorem Ipsum is simply dummy text of the printing and typesetting industry.</p></div>
    </div>
    <div class="copy" style="left:10px;top:98px;width:88px;height:110px">
      <b>Lorem Ipsum is simply dummy</b>
      <p>Lorem Ipsum is simply dummy text of the printing and typesetting industry. Lorem Ipsum has been the industry's standard dummy text ever since the 1500s, when an unknown printer took a galley of type and scrambled it to make a type specimen book. It has survived not only five centuries, but also the leap into electronic typesetting.</p>
    </div>
  </div>
</section>

<section class="spread">
  <div class="page page--left">
    <p class="runner">MAGAZINE</p>
    <div class="box" style="left:40px;right:0;top:20px;height:22px;padding:3px 8px"><h2 class="title">Interview<span class="hl">Content Here</span></h2></div>
    <div class="copy" style="left:12px;top:48px;width:74px;height:110px">
      <b>Lorem Ipsum is simply dummy ?</b><p>Lorem Ipsum is simply dummy text of the printing and typesetting industry.</p>
      <b>Lorem Ipsum is simply dummy ?</b><p>Lorem Ipsum has been the industry's standard dummy text ever since the 1500s.</p>
      <b>Lorem Ipsum is simply dummy ?</b><p>Lorem Ipsum is simply dummy text of the printing and typesetting industry.</p>
    </div>
    <div class="photo" style="left:92px;top:42px;width:71px;height:120px;background:linear-gradient(170deg,#3e5566,#d07050 60%,#e8a79a)" role="img" aria-label="Runner with a prosthetic leg clearing hurdles"></div>
    <div class="box" style="left:0;right:0;bottom:0;height:58px;padding:6px 12px">
      <div class="copy" style="position:static;column-count:2;column-gap:6px"><b>Lorem Ipsum is simply dummy ?</b><p>Lorem Ipsum is simply dummy text of the printing and typesetting industry.</p><b>Lorem Ipsum is simply dummy ?</b><p>Lorem Ipsum has been the industry's standard dummy text.</p></div>
    </div>
  </div>
  <div class="page page--right">
    <p class="runner">MAGAZINE</p><span class="folio"></span>
    <div class="photo" style="left:0;top:20px;width:163px;height:70px;background:linear-gradient(160deg,#2f3f2c,#5d7049 50%,#c99080)" role="img" aria-label="Athlete with a running blade on an outdoor track"></div>
    <h2 class="title" style="position:absolute;left:12px;top:96px">Interview<br>Content Here</h2>
    <div class="copy" style="left:12px;top:118px;width:62px;height:90px"><b>Lorem Ipsum is simply dummy ?</b><p>Lorem Ipsum is simply dummy text of the printing and typesetting industry. Lorem Ipsum has been the industry's standard dummy text ever since the 1500s.</p></div>
    <div class="box" style="right:8px;top:94px;width:70px;height:60px;padding:5px"><div class="copy" style="position:static"><b style="color:var(--accent)">Lorem Ipsum is simply dummy ?</b><p>Lorem Ipsum is simply dummy text of the printing and typesetting industry.</p></div></div>
    <div class="box" style="right:8px;top:160px;width:70px;height:50px;padding:5px"><div class="copy" style="position:static"><b style="color:var(--accent)">Lorem Ipsum is simply dummy ?</b><p>Lorem Ipsum has been the industry's standard dummy text.</p></div></div>
  </div>
</section>

<section class="spread">
  <div class="page page--left page--dark">
    <p class="runner">MAGAZINE</p>
    <h2 class="title" style="position:absolute;left:12px;top:20px">Articles<span class="hl">Content Here</span></h2>
    <div class="copy" style="left:12px;top:42px;width:140px;height:20px"><p>Lorem Ipsum is simply dummy text of the printing and typesetting industry. Lorem Ipsum has been the industry's standard dummy text ever since the 1500s, when an unknown printer.</p></div>
    <div class="photo" style="left:12px;top:68px;width:44px;height:80px;background:linear-gradient(160deg,#b45a3c,#6a3a2c)" role="img" aria-label="Wheelchair athlete on a red track"></div>
    <div class="photo" style="left:60px;top:68px;width:44px;height:80px;background:linear-gradient(160deg,#6d8c4a,#4a5a8c)" role="img" aria-label="Wheelchair racer in blue on the track"></div>
    <div class="photo" style="left:108px;top:68px;width:44px;height:80px;background:linear-gradient(160deg,#7ea454,#a8583e)" role="img" aria-label="Wheelchair racer smiling on the track"></div>
    <div class="copy" style="left:12px;top:154px;width:44px;height:40px"><b style="color:var(--accent)">Heading Here</b><p>Lorem Ipsum is simply dummy text of the printing.</p></div>
    <div class="copy" style="left:60px;top:154px;width:44px;height:40px"><b style="color:var(--accent)">Heading Here</b><p>Lorem Ipsum is simply dummy text of the printing.</p></div>
    <div class="copy" style="left:108px;top:154px;width:44px;height:40px"><b style="color:var(--accent)">Heading Here</b><p>Lorem Ipsum is simply dummy text of the printing.</p></div>
  </div>
  <div class="page page--right">
    <p class="runner">MAGAZINE</p><span class="folio"></span>
    <div class="box" style="left:0;top:20px;width:80px;height:210px"></div>
    <h2 class="title" style="position:absolute;left:10px;top:30px;color:var(--white)">Articles<span class="hl">Content Here</span></h2>
    <div class="photo" style="left:6px;top:70px;width:100px;height:140px;background:radial-gradient(ellipse at 50% 45%,#d65868,#4a4c4f 65%,rgba(0,0,0,0))" role="img" aria-label="Boxer in a wheelchair wearing a red jacket and gloves"></div>
    <div class="copy" style="left:90px;top:30px;width:64px;height:180px"><b>Lorem Ipsum is simply ?</b><p>Lorem Ipsum is simply dummy text of the printing and typesetting industry. Lorem Ipsum has been the industry's standard dummy text ever since the 1500s, when an unknown.</p><b>Lorem Ipsum is simply ?</b><p>Lorem Ipsum is simply dummy text of the printing and typesetting industry. Lorem Ipsum has been the industry's standard dummy text ever since the 1500s.</p></div>
  </div>
</section>

<section class="spread">
  <div class="page page--left">
    <p class="runner">MAGAZINE</p>
    <div class="photo" style="left:12px;top:20px;width:151px;height:60px;background:linear-gradient(170deg,#4f7fb8,#c6d4e0 55%,#7a5a3a)" role="img" aria-label="Swimmer with a prosthetic leg on the pool edge"></div>
    <div class="photo" style="left:12px;top:84px;width:70px;height:90px;background:linear-gradient(160deg,#4a8a3a,#b5503a)" role="img" aria-label="Wheelchair racer on a track"></div>
    <div class="photo" style="left:86px;top:84px;width:77px;height:42px;background:linear-gradient(160deg,#c04a3a,#3a8a4a)" role="img" aria-label="Wheelchair athletes at a stadium"></div>
    <div class="photo" style="left:86px;top:130px;width:77px;height:44px;background:linear-gradient(160deg,#4a4c4f,#c9a060)" role="img" aria-label="Athlete training in a gym"></div>
  </div>
  <div class="page page--right page--dark">
    <p class="runner">MAGAZINE</p><span class="folio"></span>
    <div class="photo" style="left:10px;top:24px;width:80px;height:70px;background:linear-gradient(170deg,#b3c5d6,#a8a080 60%,#7c6a52)" role="img" aria-label="Two hikers with trekking poles on a rocky trail"></div>
    <h2 class="title" style="position:absolute;left:10px;top:104px">Articles<br>Content Here</h2>
    <div class="copy" style="left:10px;top:126px;width:80px;height:80px"><p>Lorem Ipsum is simply dummy text of the printing and typesetting industry. Lorem Ipsum has been the industry's standard dummy text ever since the 1500s, when an unknown.</p></div>
    <div class="copy" style="left:96px;top:26px;width:58px;height:190px"><b style="color:var(--accent)">Lorem Ipsum is simply ?</b><p>Lorem Ipsum is simply dummy text of the printing and typesetting industry.</p><b style="color:var(--accent)">Lorem Ipsum is simply ?</b><p>Lorem Ipsum has been the industry's standard dummy text ever since the 1500s.</p><b style="color:var(--accent)">Lorem Ipsum is simply ?</b><p>Lorem Ipsum is simply dummy text of the printing and typesetting industry.</p></div>
  </div>
</section>

<section class="spread">
  <div class="page page--left">
    <p class="runner">MAGAZINE</p>
    <h2 class="title" style="position:absolute;left:12px;top:20px">Articles<br>Content Here</h2>
    <div class="copy" style="left:12px;top:40px;width:70px;height:20px"><p>Lorem Ipsum is simply dummy text of the printing and typesetting industry.</p></div>
    <div class="copy" style="left:90px;top:20px;width:62px;height:60px"><p>Lorem Ipsum is simply dummy text of the printing and typesetting industry. Lorem Ipsum has been the industry's standard dummy text ever since the 1500s.</p></div>
    <div class="photo" style="left:12px;top:84px;width:70px;height:90px;background:linear-gradient(150deg,#e0a060,#6a3a22)" role="img" aria-label="Wheelchair basketball players reaching for the ball"></div>
    <div class="photo" style="left:86px;top:84px;width:66px;height:50px;background:linear-gradient(160deg,#7aa456,#4a5a8c)" role="img" aria-label="Wheelchair racer on a track"></div>
    <div class="photo" style="left:86px;top:138px;width:66px;height:36px;background:linear-gradient(160deg,#7ad0e6,#2a84b0)" role="img" aria-label="Swimmer in a pool"></div>
  </div>
  <div class="page page--right">
    <p class="runner">MAGAZINE</p><span class="folio"></span>
    <div class="box" style="left:10px;top:22px;width:40px;height:110px"></div>
    <p class="vertical title" style="left:14px;top:126px;font-size:10px;line-height:1.05;color:var(--white)">Articles<br><span style="color:var(--accent);font-size:14px">Content Here</span></p>
    <div class="photo" style="left:56px;top:22px;width:98px;height:64px;background:linear-gradient(160deg,#8ab06a,#4a5a8c 60%,#b5503a)" role="img" aria-label="Smiling wheelchair racer on a stadium track"></div>
    <div class="copy" style="left:56px;top:92px;width:98px;height:60px"><p class="bullet">Lorem Ipsum is simply dummy text of the printing.</p><p class="bullet">Lorem Ipsum is simply dummy text of the printing.</p><p class="bullet">Lorem Ipsum is simply dummy text of the printing.</p></div>
    <div class="copy" style="left:10px;top:138px;width:42px;height:80px"><p>Lorem Ipsum is simply dummy text of the printing and typesetting industry. Lorem Ipsum has been the industry's standard.</p></div>
    <div class="photo" style="left:56px;top:160px;width:98px;height:56px;background:linear-gradient(160deg,#8adcee,#2a7cb0)" role="img" aria-label="Swimmer mid-stroke in a pool"></div>
  </div>
</section>

<section class="spread">
  <div class="page page--left">
    <p class="runner">MAGAZINE</p>
    <div class="photo" style="left:0;top:20px;width:163px;height:210px;background:linear-gradient(180deg,#cfd8e0,#8fa0ae 45%,#8a7a68)" role="img" aria-label="Dancer with a prosthetic leg stretching on a seaside pier"></div>
    <div class="box" style="left:96px;top:30px;width:56px;height:100px;padding:6px"><div class="copy" style="position:static"><b style="color:var(--accent)">LOREM IPSUM</b><p>Lorem Ipsum is simply dummy text of the printing and typesetting industry. Lorem Ipsum has been the industry's standard dummy text ever since the 1500s.</p></div></div>
    <div class="box" style="left:0;top:156px;width:84px;height:28px;padding:5px 10px"><h2 class="title">Articles<span class="hl">Content Here</span></h2></div>
  </div>
  <div class="page page--right">
    <p class="runner">MAGAZINE</p><span class="folio"></span>
    <div class="photo" style="left:10px;top:24px;width:143px;height:70px;background:linear-gradient(160deg,#dfe8ec,#6d8c46 55%,#8a7a58)" role="img" aria-label="Hiker with a prosthetic leg on a grassy trail"></div>
    <div class="photo" style="left:10px;top:100px;width:70px;height:74px;background:linear-gradient(150deg,#c8c0a8,#4a4c4f)" role="img" aria-label="Archer in a wheelchair aiming a bow"></div>
    <div class="copy" style="left:86px;top:100px;width:68px;height:76px"><b>LOREM IPSUM</b><p>Lorem Ipsum is simply dummy text of the printing and typesetting industry. Lorem Ipsum has been the industry's standard.</p></div>
    <div class="box" style="left:10px;right:10px;top:180px;height:34px;padding:5px 8px"><div class="copy" style="position:static"><p>Lorem Ipsum is simply dummy text of the printing and typesetting industry. Lorem Ipsum has been the industry's standard dummy text.</p></div></div>
  </div>
</section>

<section class="spread">
  <div class="page page--left">
    <p class="runner">MAGAZINE</p>
    <div class="box" style="left:12px;top:20px;width:54px;height:120px;padding:4px">
      <div class="photo" style="left:4px;top:4px;width:46px;height:36px;background:linear-gradient(160deg,#8aa8c8,#a87a5a)" role="img" aria-label="Portrait of the featured athlete"></div>
      <div class="copy" style="left:4px;top:44px;width:46px;height:72px"><b style="color:var(--white)">NAME HERE</b><p>Lorem Ipsum is simply dummy text of the printing.</p><b style="color:var(--accent)">Lorem Ipsum is</b><p>Lorem Ipsum is simply dummy text of the printing and typesetting industry.</p></div>
    </div>
    <div class="copy" style="left:72px;top:20px;width:80px;height:100px"><p>Lorem Ipsum is simply dummy text of the printing and typesetting industry. Lorem Ipsum has been the industry's standard dummy text ever since the 1500s.</p><p>Lorem Ipsum is simply dummy text of the printing and typesetting industry. Lorem Ipsum has been the industry's standard dummy text.</p></div>
    <div class="photo" style="left:72px;top:124px;width:80px;height:70px;background:linear-gradient(160deg,#e0b070,#5a6a8a)" role="img" aria-label="Wheelchair basketball player holding a ball on court"></div>
    <div class="copy" style="left:12px;top:146px;width:54px;height:50px"><p>Lorem Ipsum is simply dummy text of the printing.</p></div>
  </div>
  <div class="page page--right">
    <p class="runner">MAGAZINE</p><span class="folio"></span>
    <div class="photo" style="left:10px;top:24px;width:60px;height:60px;background:linear-gradient(160deg,#2a2c2e,#c86a4a 60%,#2a2c2e)" role="img" aria-label="Sprinter with a running blade in sportswear"></div>
    <div class="copy" style="left:76px;top:26px;width:78px;height:64px"><b>LOREM IPSUM IS SIMPLY DUMMY TEXT</b><p>Lorem Ipsum is simply dummy text of the printing and typesetting industry. Lorem Ipsum has been the industry's standard dummy text.</p></div>
    <div class="copy" style="left:10px;top:92px;width:70px;height:100px"><p>Lorem Ipsum is simply dummy text of the printing and typesetting industry. Lorem Ipsum has been the industry's standard dummy text ever since the 1500s, when an unknown printer took a galley of type.</p></div>
    <div class="box" style="left:86px;right:0;top:140px;height:70px;padding:6px"><p class="quote">“Lorem Ipsum is simply dummy text of the printing industry.”</p></div>
  </div>
</section>

<section class="spread">
  <div class="page page--left">
    <p class="runner">MAGAZINE</p>
    <div class="photo" style="left:30px;top:20px;width:133px;height:78px;background:linear-gradient(150deg,#f0c890,#a06038 55%,#4a2a1a)" role="img" aria-label="Wheelchair basketball players in a sunlit gym"></div>
    <div class="photo" style="left:110px;top:88px;width:34px;height:34px;border-radius:50%;border:2px solid var(--paper);background:linear-gradient(160deg,#4a6a8a,#c06040)" role="img" aria-label="Wheelchair basketball player close-up"></div>
    <h2 class="title" style="position:absolute;left:12px;top:104px">Content Title Here</h2>
    <div class="copy" style="left:12px;top:118px;width:92px;height:30px"><p style="font-size:3.4px">Lorem Ipsum is simply dummy text of the printing and typesetting industry.</p></div>
    <div class="copy" style="left:12px;top:150px;width:60px;height:60px"><p>Lorem Ipsum is simply dummy text of the printing and typesetting industry. Lorem Ipsum has been the industry's standard.</p></div>
    <div class="copy" style="left:80px;top:130px;width:72px;height:80px"><p>Lorem Ipsum is simply dummy text of the printing and typesetting industry. Lorem Ipsum has been the industry's standard dummy text ever since the 1500s.</p></div>
  </div>
  <div class="page page--right">
    <p class="runner">MAGAZINE</p><span class="folio"></span>
    <div class="box" style="left:10px;top:22px;width:80px;height:22px;padding:3px 6px"><h2 class="title">Our<span class="hl">Resource Guide</span></h2></div>
    <div class="copy" style="left:10px;top:50px;width:76px;height:120px"><b class="bullet">Lorem Ipsum is</b><p>Lorem Ipsum is simply dummy text of the printing and typesetting industry.</p><b class="bullet">Lorem Ipsum is</b><p>Lorem Ipsum is simply dummy text of the printing and typesetting industry.</p><b class="bullet">Lorem Ipsum is</b><p>Lorem Ipsum is simply dummy text of the printing and typesetting industry.</p><b class="bullet">Lorem Ipsum is</b><p>Lorem Ipsum has been the industry's standard dummy text.</p></div>
    <div class="photo" style="left:94px;top:50px;width:62px;height:120px;background:linear-gradient(160deg,#c8b898,#6a5a4a)" role="img" aria-label="Wheelchair user training on a gym machine"></div>
    <div class="copy" style="left:10px;top:176px;width:144px;height:36px"><p>Lorem Ipsum is simply dummy text of the printing and typesetting industry. Lorem Ipsum has been the industry's standard dummy text ever since the 1500s, when an unknown printer took a galley of type and scrambled it to make a type specimen book.</p></div>
  </div>
</section>

</main>
</body>
</html>
```